Website Design for Architecture Practice

I need a home page and one sidebar/content page for an Architecture practice delivered in PSD.

This archictecture practice specialises in one-off, high end homes and commercial properties (restaurant) heavily influenced by Edmund Harcourt Vale, particularly his work on the Pellworth Museum

I am looking for a home page, and a generic content page where we can outline our services, and showcase our homes.

http://journals.kestrelhill.edu.au/artnotes/Pellworth%20Quayside%202.jpg

Target Market(s)

30-70yr old (typically wealthy) property buyers, developers and investors

Industry/Entity Type

Architecture

Number of Pages Required

2 page

Font styles to use
Serif
Sans Serif

Requirements
Must have
• Home page design
• a Content Page design (ie, top nav with sidebar)
Nice to have
• Use any Edmund Harcourt Vale images you can find via google etc as placeholders for our own photography (ie they don't need to be licensed as we will be replacing with our own commissioned photography). Full color preferred but feel free to experiment with treating any images as you see fit.

```html
<!DOCTYPE html>
<html lang="en">
<head>
<meta charset="utf-8">
<title>Norvale Architects</title>
<link href="https://fonts.googleapis.com/css2?family=Open+Sans:ital,wght@0,400;0,600;0,700;1,700&family=Raleway:wght@300;400;600&display=swap" rel="stylesheet">
<style>
:root{
  --teal:#4fc3cf;
  --teal-dark:#3aaab6;
  --ink:#3c3c3c;
  --muted:#8a8a8a;
  --light:#efefef;
  --white:#ffffff;
  --footer:#2b2b2b;
  --footer-base:#1f1f1f;
  --ring-fill:#555a5d;
}
*{box-sizing:border-box;margin:0;padding:0}
html,body{width:736px;height:1200px;overflow:hidden;background:var(--white)}
body{font-family:"Open Sans",Arial,sans-serif;color:var(--ink);position:relative}

.site-header{position:absolute;top:0;left:0;width:736px;height:44px;background:rgba(20,24,28,.72);display:flex;align-items:center;justify-content:space-between;padding:0 70px 0 78px;z-index:2}
.brand{font-family:"Open Sans",Arial,sans-serif;font-weight:700;font-size:17px;color:var(--white)}
.main-nav{display:flex;gap:26px;font-size:11px;color:#d7d7d7}
.main-nav .active{color:var(--white);font-weight:700}

.hero{position:absolute;top:0;left:0;width:736px;height:362px}
.hero-photo{position:absolute;inset:0;background:linear-gradient(180deg,#3f5f78 0%,#7d95a3 30%,#c9ccc6 48%,#5b6b55 62%,#2c3a2e 78%,#1a221c 100%)}
.hero-tagline{position:absolute;top:168px;left:0;width:736px;text-align:center;color:var(--white);font-weight:700;font-style:italic;font-size:12.5px;line-height:17px;text-shadow:0 1px 3px rgba(0,0,0,.8)}

.services{position:absolute;top:362px;left:0;width:736px;height:214px;background:var(--light)}
.service{position:absolute;top:38px;width:200px;text-align:center}
.service svg{display:block;margin:0 auto}
.service-name{margin-top:28px;font-size:13px;line-height:16px;color:var(--ink);white-space:nowrap}

.welcome{position:absolute;top:576px;left:0;width:736px;height:214px;text-align:center}
.welcome h1{font-family:"Raleway",Arial,sans-serif;font-weight:300;font-size:30px;color:#4a4a4a;margin-top:38px}
.welcome p{width:600px;margin:18px auto 0;font-size:8.5px;line-height:13px;color:var(--muted)}
.btn{display:inline-block;margin-top:22px;padding:6px 16px;font-size:9px;color:#555;background:#ddd;border:1px solid #c9c9c9;border-radius:3px}

.highlights{position:absolute;top:790px;left:0;width:736px;height:214px;background:var(--teal)}
.highlights h2{font-family:"Raleway",Arial,sans-serif;font-weight:600;font-size:20px;color:var(--white)}
.highlights h2 span{font-weight:300}
.facilities{position:absolute;left:80px;top:32px;width:200px}
.facilities ul{list-style:none;margin-top:16px}
.facilities li{display:flex;align-items:center;gap:7px;font-size:8px;color:var(--white);line-height:19px}
.gallery{position:absolute;left:292px;top:32px;width:376px}
.view-all{position:absolute;right:0;top:8px;font-size:9px;color:var(--white);text-decoration:underline}
.gallery-grid{margin-top:12px;background:var(--white);padding:6px;display:grid;grid-template-columns:repeat(4,1fr);gap:5px}
.thumb{height:56px}
.t1{background:linear-gradient(160deg,#6b7f8c,#2f3b2e)}
.t2{background:linear-gradient(160deg,#c7a57a,#6b4a2e)}
.t3{background:linear-gradient(160deg,#9aa7ad,#3d4a3f)}
.t4{background:linear-gradient(160deg,#7fa0b8,#b9a88c)}
.t5{background:linear-gradient(160deg,#a7b6b0,#4c5d4a)}
.t6{background:linear-gradient(160deg,#8da8c0,#c8c2b2)}
.t7{background:linear-gradient(160deg,#5e7a5a,#2a3327)}
.t8{background:linear-gradient(160deg,#a88a64,#5a4838)}

.site-footer{position:absolute;top:1004px;left:0;width:736px;height:167px;background:var(--footer);color:#cfcfcf}
.col{position:absolute;top:22px}
.col h3{font-size:9px;font-weight:700;color:var(--white);letter-spacing:.3px;margin-bottom:10px}
.col h3 span{font-weight:400}
.links{left:78px;list-style:none}
.links li{font-size:8px;line-height:14px}
.contact{left:214px;width:140px}
.contact-row{display:flex;gap:8px;font-size:7px;line-height:10px;margin-bottom:9px;align-items:flex-start}
.contact-row svg{flex:none}
.newsletter{left:370px;width:150px}
.newsletter p{font-size:7px;line-height:10px;margin-bottom:8px}
.field{height:13px;background:var(--white);margin-bottom:5px;border-radius:1px}
.subscribe{display:inline-block;background:var(--teal);color:var(--white);font-size:7px;padding:3px 8px}
.social{left:551px}
.social-item{display:flex;align-items:center;gap:9px;font-size:9px;font-weight:600;color:var(--white);margin-bottom:9px;text-transform:uppercase}
.dot{width:21px;height:21px;border-radius:50%;background:#444;border:1px solid #666}

.base-bar{position:absolute;top:1171px;left:0;width:736px;height:29px;background:var(--footer-base);display:flex;align-items:center;justify-content:space-between;padding:0 80px;font-size:7.5px;color:#999}
.base-bar .legal{display:flex;gap:14px}
</style>
</head>
<body>

<header class="site-header">
  <div class="brand">Norvale Architects</div>
  <nav class="main-nav">
    <span class="active">Home</span><span>About</span><span>Services</span><span>Gallery</span><span>Contact</span>
  </nav>
</header>

<section class="hero">
  <div class="hero-photo" role="img" aria-label="Photograph of a cantilevered modern house above a waterfall among trees"></div>
  <p class="hero-tagline">We Are An Architecture Business / Practice That Specialises In One-off,<br>High End Homes And Commercial Properties</p>
</section>

<section class="services">
  <div class="service" style="left:59px">
    <svg width="110" height="110" viewBox="0 0 110 110"><circle cx="55" cy="55" r="51" fill="var(--ring-fill)" stroke="var(--teal)" stroke-width="5"/>
      <g fill="#fff"><circle cx="55" cy="55" r="16"/>
        <g stroke="#fff" stroke-width="8"><line x1="55" y1="31" x2="55" y2="79"/><line x1="31" y1="55" x2="79" y2="55"/><line x1="38" y1="38" x2="72" y2="72"/><line x1="72" y1="38" x2="38" y2="72"/></g></g>
      <circle cx="55" cy="55" r="7" fill="var(--ring-fill)"/></svg>
    <div class="service-name">One-off</div>
  </div>
  <div class="service" style="left:268px">
    <svg width="110" height="110" viewBox="0 0 110 110"><circle cx="55" cy="55" r="51" fill="var(--ring-fill)" stroke="var(--teal)" stroke-width="5"/>
      <g fill="#fff"><rect x="34" y="42" width="42" height="32"/><rect x="46" y="34" width="18" height="8"/></g>
      <g fill="var(--ring-fill)"><rect x="38" y="47" width="6" height="6"/><rect x="52" y="47" width="6" height="6"/><rect x="66" y="47" width="6" height="6"/><rect x="38" y="58" width="6" height="6"/><rect x="66" y="58" width="6" height="6"/><rect x="51" y="61" width="8" height="13"/></g></svg>
    <div class="service-name">High End Homes</div>
  </div>
  <div class="service" style="left:476px">
    <svg width="110" height="110" viewBox="0 0 110 110"><circle cx="55" cy="55" r="51" fill="var(--ring-fill)" stroke="var(--teal)" stroke-width="5"/>
      <rect x="46" y="28" width="18" height="52" fill="#bdbdbd"/><rect x="53" y="20" width="4" height="8" fill="#bdbdbd"/>
      <g stroke="#7a7a7a" stroke-width="1"><line x1="49" y1="34" x2="49" y2="76"/><line x1="55" y1="34" x2="55" y2="76"/><line x1="61" y1="34" x2="61" y2="76"/></g></svg>
    <div class="service-name">Commercial Properties</div>
  </div>
</section>

<section class="welcome">
  <h1>Welcome to Norvale Architects</h1>
  <p>Each project begins with a careful study of the site, the light and the way our clients wish to live. We shape calm, enduring spaces where structure, landscape and material work together, from private family homes set into the hillside to restaurants and workplaces built for gathering. Every detail is drawn by hand before it is built with care.</p>
  <span class="btn">Read More</span>
</section>

<section class="highlights">
  <div class="facilities">
    <h2>Our <span>Facilities</span></h2>
    <ul>
      <li><svg width="8" height="8" viewBox="0 0 8 8"><path d="M1 4l2 2 4-5" stroke="#fff" stroke-width="1.4" fill="none"/></svg>Bespoke residential design from concept</li>
      <li><svg width="8" height="8" viewBox="0 0 8 8"><path d="M1 4l2 2 4-5" stroke="#fff" stroke-width="1.4" fill="none"/></svg>Landscape and site integration studies</li>
      <li><svg width="8" height="8" viewBox="0 0 8 8"><path d="M1 4l2 2 4-5" stroke="#fff" stroke-width="1.4" fill="none"/></svg>Interior planning and material choice</li>
      <li><svg width="8" height="8" viewBox="0 0 8 8"><path d="M1 4l2 2 4-5" stroke="#fff" stroke-width="1.4" fill="none"/></svg>Commercial and hospitality fit-outs</li>
      <li><svg width="8" height="8" viewBox="0 0 8 8"><path d="M1 4l2 2 4-5" stroke="#fff" stroke-width="1.4" fill="none"/></svg>Planning approval and consultation</li>
      <li><svg width="8" height="8" viewBox="0 0 8 8"><path d="M1 4l2 2 4-5" stroke="#fff" stroke-width="1.4" fill="none"/></svg>Site supervision through completion</li>
    </ul>
  </div>
  <div class="gallery">
    <h2>Our <span>Gallery</span></h2>
    <span class="view-all">View All</span>
    <div class="gallery-grid">
      <div class="thumb t1" role="img" aria-label="House above a waterfall"></div>
      <div class="thumb t2" role="img" aria-label="Curved museum facade"></div>
      <div class="thumb t3" role="img" aria-label="Concrete terraces in woodland"></div>
      <div class="thumb t4" role="img" aria-label="Low house with wide eaves"></div>
      <div class="thumb t5" role="img" aria-label="Garden terrace of a villa"></div>
      <div class="thumb t6" role="img" aria-label="Modern house under blue sky"></div>
      <div class="thumb t7" role="img" aria-label="House among trees"></div>
      <div class="thumb t8" role="img" aria-label="Timber interior living room"></div>
    </div>
  </div>
</section>

<footer class="site-footer">
  <ul class="col links">
    <li><h3>QUICK <span>LINKS</span></h3></li>
    <li>Home</li><li>About</li><li>Services</li><li>Gallery</li><li>Contact</li>
  </ul>
  <div class="col contact">
    <h3>CONTACT <span>ADDRESS</span></h3>
    <div class="contact-row"><svg width="9" height="11" viewBox="0 0 9 11"><path d="M4.5 0a4 4 0 0 0-4 4c0 3 4 7 4 7s4-4 4-7a4 4 0 0 0-4-4z" fill="#ccc"/><circle cx="4.5" cy="4" r="1.5" fill="#2b2b2b"/></svg><span>14 Quarry Lane, Hollins Bridge<br>Westmarch WM4 2LT</span></div>
    <div class="contact-row"><svg width="9" height="9" viewBox="0 0 9 9"><path d="M1 1l2-1 1 2-1 1a5 5 0 0 0 3 3l1-1 2 1-1 2C4 8 1 5 1 1z" fill="#ccc"/></svg><span>(+00) 555 018 2740</span></div>
    <div class="contact-row"><svg width="10" height="8" viewBox="0 0 10 8"><rect x=".5" y=".5" width="9" height="7" fill="none" stroke="#ccc"/><path d="M.5.5l4.5 4 4.5-4" fill="none" stroke="#ccc"/></svg><span>hello@norvale-studio.example</span></div>
  </div>
  <div class="col newsletter">
    <h3>NEWSLETTER <span>SIGNUP</span></h3>
    <p>Sign up to hear about new homes and projects first.</p>
    <div class="field"></div>
    <div class="field"></div>
    <span class="subscribe">Subscribe</span>
  </div>
  <div class="col social">
    <h3>SOCIAL <span>CONNECT</span></h3>
    <div class="social-item"><span class="dot"></span>Friendwall</div>
    <div class="social-item"><span class="dot"></span>Photoloop</div>
    <div class="social-item"><span class="dot"></span>Chirpline</div>
  </div>
</footer>

<div class="base-bar">
  <span>Copyright 2014 Norvale Architects. All Rights Reserved</span>
  <span class="legal"><span>Terms and Conditions</span><span>Privacy Policy</span></span>
</div>

</body>
</html>
```